Business Card Design

Online clothing womens clothing store, I sell my clothing online and at the markets.

i would like the attached picture on the front of the card and the contact information on the back.

Industry/Entity Type

Business

Contact Information for Business Card

Marlow Thread
Karen Whitfield
(Instagram symbol) _marlow_thread_
(Facebook symbol) www.fakebookexample.com/marlowthreadau/

W : www.marlowthread.example.au
E : info@marlowthread.example.au
P : 0498716204

```html
<!DOCTYPE html>
<html lang="en">
<head>
<meta charset="utf-8">
<title>Marlow Thread – Business Card</title>
<link href="https://fonts.googleapis.com/css2?family=Raleway:wght@200;300;400&display=swap" rel="stylesheet">
<style>
  :root{
    --page:#e9e7e3;
    --card-black:#0c0c0c;
    --ink-white:#f4f4f4;
    --band:rgba(20,20,20,0.78);
    --shadow:rgba(0,0,0,0.28);
  }
  *{box-sizing:border-box;margin:0;padding:0}
  html,body{width:1200px;height:858px;overflow:hidden;background:var(--page)}
  body{font-family:"Raleway",sans-serif;color:var(--ink-white)}
  .sheet{position:relative;width:1200px;height:858px}
  .card{position:absolute;left:285px;width:630px;height:360px;overflow:hidden;
        box-shadow:0 10px 26px var(--shadow)}
  .card--back{top:49px;background:var(--card-black)}
  .card--front{top:449px}

  /* back side */
  .brand{position:absolute;left:52px;top:72px;font-weight:200;font-size:42px;
         letter-spacing:9px;text-transform:uppercase;white-space:nowrap;line-height:1}
  .owner{position:absolute;left:56px;top:240px;font-weight:300;font-size:21px;letter-spacing:2.5px;white-space:nowrap}
  .divider{position:absolute;left:300px;top:182px;width:2px;height:118px;background:var(--ink-white)}
  .contacts{position:absolute;left:330px;top:172px;list-style:none}
  .contacts li{display:flex;align-items:center;gap:10px;font-weight:400;font-size:15px;
               line-height:24.5px;white-space:nowrap}
  .contacts svg{width:13px;height:13px;flex:none}

  /* front side */
  .photo{position:absolute;inset:0;
         background:linear-gradient(100deg,#7d8a6a 0%,#b7b2a6 22%,#d9d6d1 45%,#f1f1ef 70%,#cfd6da 100%)}
  .band{position:absolute;left:0;right:0;top:118px;height:124px;background:var(--band);
        display:flex;align-items:center}
  .band .brand{position:static;display:block;padding-left:44px;font-size:46px;letter-spacing:11px}
</style>
</head>
<body>
<main class="sheet">

  <section class="card card--back" aria-label="Card back">
    <div class="brand">Marlow Thread</div>
    <div class="owner">Karen Whitfield</div>
    <div class="divider"></div>
    <ul class="contacts">
      <li><svg viewBox="0 0 13 13"><rect width="13" height="13" rx="2" fill="#f4f4f4"/><path d="M4 3l1.6 0 .6 2-1 .8a6 6 0 0 0 2.2 2.2l.8-1 2 .6V10C6.5 10 3 6.5 4 3z" fill="#0c0c0c"/></svg>0498716204</li>
      <li><svg viewBox="0 0 13 13"><rect width="13" height="13" rx="2" fill="#f4f4f4"/><rect x="3" y="4" width="7" height="5" fill="none" stroke="#0c0c0c" stroke-width="1"/><path d="M3 4l3.5 3L10 4" fill="none" stroke="#0c0c0c" stroke-width="1"/></svg>info@marlowthread.example.au</li>
      <li><svg viewBox="0 0 13 13"><rect width="13" height="13" rx="2" fill="#f4f4f4"/><circle cx="6.5" cy="6.5" r="3.3" fill="none" stroke="#0c0c0c" stroke-width="1"/><path d="M3.2 6.5h6.6" stroke="#0c0c0c" stroke-width="1"/></svg>www.marlowthread.example.au</li>
      <li><svg viewBox="0 0 13 13"><rect width="13" height="13" rx="2" fill="#f4f4f4"/></svg>marlowthreadau</li>
      <li><svg viewBox="0 0 13 13"><rect width="13" height="13" rx="2" fill="#f4f4f4"/></svg>marlow_thread</li>
    </ul>
  </section>

  <section class="card card--front" aria-label="Card front">
    <div class="photo" role="img" aria-label="Photo of two women in casual boho outfits seated on a bright verandah with garden and hills behind"></div>
    <div class="band"><span class="brand">Marlow Thread</span></div>
  </section>

</main>
</body>
</html>
```